Im want a website LIKE VRX's and FleetHollow.com's with product payment options like Trenzo's

I need a website LIKE VRX with a header made EXACTLY LIKE THAT OF FLEETHOLLOWS .

The front page photo should be like that of FLEETHOLLOW's webpage as well.

The name of the website will be called "M.K. (Caldera Key)".

We will be targeting ALL MARKETS in a small town in central Panama and charging businesses "listing fees" like a phone book does but also providing informational blogs, news, and other interesting activities.

THIS IS A MULTI PAGE WEBSITE

THIS IS WHERE VRX's website meets Brivelle/FleetHollow.

Once the layout is built I will tweak and modify, add information, and upload items for sale.

Here is a list of specific categories that should be listed out above the front page header image/search bar

-- Home -- News -- Travel -- Activities -- Shop & Dine -- Store -- More... --

These categories should be spread across the bottom of the page in three sections:

WHATS SO GREAT ABOUT (Caldera Key),
HAND PICKED TOURS
ACTIVITIES etc.

Also lets use www.Trenzo.example 's
"HOT DESTINATIONS"
"BEAT THE BEST PRICES IN BOQUETE"
"OCTOBERS INSIDER PICKS"
"TOP DESTINATIONS"
and spread them in four sections side-by-side near the bottom of the page.

Overall I would like to see the finished product to be something LIKE VRX's and FleetHollows.

WE NEED ONLINE PAYMENT OPTIONS LIKE BRIVELLE'S WEBSITE HAS

This will be a desktop website but should be very mobile friendly as well.

-rodmund

P.S. Good luck!

If it isn't already too late to change the website name, the name of the website should be "Caldera Key". Added Friday, October 9, 2015

What do you guys think the budget should be to win this? Added Saturday, October 10, 2015

www.palmorra.example is the most amazing simple site. Whoever can make me a replica with my specifications will win immediately!!!! Added Sunday, October 18, 2015

OMG www.palmorra.example is the bomb!So simple and elegant. Whoever can make me an EXACT REPLICA OF WWW.PALMORRA.EXAMPLE as my site with the specifications mentioned in my brief will take home the $825.00 immediately! Good luck amigos! Added Sunday, October 18, 2015

Does anybody know how to add recurring monthly billing options on this website? Added Sunday, October 18, 2015

ALL MARKETS

Product

Coded - Design and coding required

5+ page

• Coinvey payment options.
• I must be able to add and remove photos/text and video from the HTML files in the page.
• Be creative my friends, and may the odds be forever in your favor!
• I added some photos of a good layout for our page below.

```html
<!DOCTYPE html>
<html lang="en">
<head>
<meta charset="utf-8">
<title>Caldera Key</title>
<link href="https://fonts.googleapis.com/css2?family=Open+Sans:wght@400;600;700;800&display=swap" rel="stylesheet">
<style>
:root{
  --teal-dark:#17505b;
  --teal-deeper:#123f48;
  --teal:#1f8fa3;
  --orange:#f47b20;
  --ink:#333c40;
  --muted:#8a9296;
  --line:#e3e6e8;
  --cream:#f8f5ee;
  --white:#ffffff;
}
*{box-sizing:border-box;margin:0;padding:0}
html,body{width:1200px;height:2472px;overflow:hidden}
body{font-family:"Open Sans",Arial,sans-serif;color:var(--ink);background:var(--white);font-size:12px}
a{color:inherit;text-decoration:none}
ul{list-style:none}

/* top bar */
.topbar{height:32px;background:var(--teal-dark);color:#cfe3e6;font-size:11px;display:flex;align-items:center;justify-content:space-between;padding:0 100px}
.topbar .contact,.topbar .account{display:flex;gap:26px;align-items:center}
.topbar svg{width:11px;height:11px;vertical-align:-1px;margin-right:6px;fill:#cfe3e6}

/* header */
.site-header{height:72px;display:flex;align-items:center;justify-content:space-between;padding:0 100px;border-bottom:1px solid var(--line)}
.brand{display:flex;align-items:center;gap:10px;font-size:26px;font-weight:700;color:var(--teal)}
.brand .mark{width:18px;height:18px;border-radius:50%;background:var(--orange)}
.main-nav{display:flex;height:72px}
.main-nav a{display:flex;align-items:center;padding:0 20px;font-size:11px;font-weight:700;letter-spacing:.5px;color:var(--ink)}
.main-nav a.active{background:var(--orange);color:var(--white)}

/* hero */
.hero{position:relative;height:640px;background:linear-gradient(180deg,#7fc4e8 0%,#a9dcef 38%,#3db7c4 62%,#e9dcc0 100%)}
.hero-slider{position:absolute;left:140px;top:40px;width:920px;height:520px;border:6px solid rgba(255,255,255,.85);background:linear-gradient(180deg,#6fa9d8 0%,#b9d7ea 40%,#8ea8b8 55%,#2d6e8a 70%,#1f5670 100%)}
.hero-caption{position:absolute;right:80px;bottom:90px;color:var(--white);text-align:left}
.hero-caption h2{font-size:46px;font-weight:800;letter-spacing:1px;line-height:1.05}
.hero-caption p{font-size:26px;font-weight:600;letter-spacing:1px;margin-top:6px}
.slider-arrows{position:absolute;right:22px;bottom:18px;display:flex;gap:8px}
.slider-arrows span{width:26px;height:26px;border-radius:50%;background:rgba(0,0,0,.45);display:flex;align-items:center;justify-content:center}
.slider-arrows svg{width:10px;height:10px;stroke:#fff;stroke-width:2;fill:none}

/* welcome */
.welcome{height:190px;text-align:center;padding-top:38px}
.welcome h1{font-size:30px;font-weight:400;color:var(--ink)}
.welcome h1 span{color:var(--teal);font-weight:600}
.welcome p{width:900px;margin:18px auto 0;font-size:11.5px;line-height:1.75;color:var(--muted)}

/* features */
.features{height:250px;display:flex;gap:50px;padding:40px 100px 0}
.feature{flex:1;background:var(--cream);height:200px;position:relative;text-align:center;padding:58px 26px 0}
.feature .icon{position:absolute;left:50%;top:-34px;transform:translateX(-50%);width:68px;height:68px;border-radius:50%;display:flex;align-items:center;justify-content:center}
.feature .icon svg{width:30px;height:30px;fill:none;stroke:#fff;stroke-width:2}
.icon.gold{background:#f5b21b}.icon.blue{background:#2a9be0}.icon.green{background:#2cc2a6}
.feature h3{font-size:12px;font-weight:700;color:var(--orange);letter-spacing:.4px}
.feature p{font-size:11px;color:var(--muted);line-height:1.6;margin-top:10px}
.feature .more{display:inline-block;margin-top:18px;font-size:11px;font-weight:600;color:var(--ink);border-top:1px solid var(--line);padding-top:12px;width:100%}

/* hot destinations */
.hot{height:870px;display:flex;gap:60px;padding:14px 100px 0}
.hot-list{width:720px}
.section-title{font-size:22px;font-weight:600;color:var(--ink);padding-bottom:12px;border-bottom:1px solid var(--line)}
.trip{display:flex;gap:30px;padding:22px 0;border-bottom:1px solid var(--line);height:254px}
.trip-photo{position:relative;width:300px;height:208px;flex:none;overflow:hidden}
.trip-photo::after{content:"";position:absolute;left:0;top:0;border-top:60px solid var(--orange);border-right:60px solid transparent}
.photo-a{background:linear-gradient(180deg,#f6a35b,#f7c98a 45%,#a66a3a)}
.photo-b{background:linear-gradient(180deg,#f3c27a,#e58a4a 50%,#8a5a3e)}
.photo-c{background:linear-gradient(180deg,#5a9fd6,#c9dbe8 45%,#6c8c5a 70%,#3f6d82)}
.trip-body{padding-top:6px}
.trip-body h3{font-size:14px;font-weight:700;color:var(--teal);letter-spacing:.3px}
.trip-meta{display:flex;gap:18px;align-items:center;margin-top:10px;font-size:11px;color:var(--muted)}
.trip-meta b{color:var(--orange);font-size:14px}
.trip-body p{font-size:11px;line-height:1.7;color:var(--muted);margin-top:12px}
.btn-outline{display:inline-block;margin-top:18px;border:1px solid #cfd4d6;padding:8px 16px;font-size:10px;font-weight:700;color:var(--ink)}

.sidebar{width:220px;padding-top:56px}
.widget{border:1px solid var(--line);padding:18px 16px 20px;background:#fbfbfb}
.widget h4{text-align:center;font-size:12px;font-weight:700;color:var(--teal);letter-spacing:.5px}
.widget .intro{text-align:center;font-size:10.5px;color:var(--muted);line-height:1.6;margin-top:10px}
.field{display:flex;justify-content:space-between;align-items:center;margin-top:12px;font-size:9.5px;font-weight:600;color:var(--ink)}
.field span.box{width:110px;height:24px;border:1px solid #d6dadc;background:#fff}
.widget .note{font-size:10px;color:var(--muted);text-align:center;margin-top:16px}
.btn-orange{display:block;width:110px;margin:12px auto 0;background:var(--orange);color:#fff;font-size:10px;font-weight:700;text-align:center;padding:9px 0}
.side-photo{margin-top:40px;height:210px;background:linear-gradient(180deg,#f2b85a,#e68a3a 45%,#4a6f8a)}
.side-text{font-size:10.5px;color:var(--muted);line-height:1.6;margin-top:12px}

/* newsletter */
.newsletter{height:88px;background:var(--orange);display:flex;align-items:center;justify-content:space-between;padding:0 160px 0 210px;color:#fff}
.newsletter h4{font-size:18px;font-weight:600;letter-spacing:.5px}
.newsletter small{font-size:10.5px;opacity:.9}
.subscribe{display:flex}
.subscribe span{width:300px;height:38px;background:#fff;color:var(--muted);font-size:11px;display:flex;align-items:center;padding-left:14px}
.subscribe b{background:#222;color:#fff;font-size:11px;padding:0 22px;display:flex;align-items:center}

/* footer */
.site-footer{height:278px;background:var(--teal-dark);display:flex;gap:50px;padding:34px 100px 0;color:#b9d0d4}
.site-footer h5{font-size:13px;font-weight:600;color:#fff;margin-bottom:16px}
.site-footer .about{width:300px}
.site-footer .about h5{font-size:20px}
.site-footer .about p{font-size:10.5px;line-height:1.75}
.site-footer .col{width:170px}
.site-footer li{font-size:10.5px;line-height:2.1}
.site-footer li::before{content:"›";margin-right:8px;color:var(--orange)}
.site-footer .contact li::before{content:none}
.bottom-bar{height:52px;background:var(--teal-deeper);display:flex;align-items:center;justify-content:space-between;padding:0 100px;font-size:10.5px;color:#9fb9be}
</style>
</head>
<body>

<div class="topbar">
  <div class="contact">
    <span><svg viewBox="0 0 24 24"><path d="M6.6 10.8a15 15 0 0 0 6.6 6.6l2.2-2.2c.3-.3.7-.4 1-.2 1.1.4 2.3.6 3.6.6.6 0 1 .4 1 1V20c0 .6-.4 1-1 1A17 17 0 0 1 3 4c0-.6.4-1 1-1h3.5c.6 0 1 .4 1 1 0 1.3.2 2.5.6 3.6.1.3 0 .7-.2 1z"/></svg>+507 555 0142</span>
    <span><svg viewBox="0 0 24 24"><path d="M2 5h20v14H2z M2 5l10 8 10-8" stroke="#cfe3e6" stroke-width="2" fill="none"/></svg>hello@calderakey.example</span>
  </div>
  <div class="account"><span>LOG IN / REGISTER</span><span>ENGLISH ▾</span></div>
</div>

<header class="site-header">
  <a class="brand" href="#"><span class="mark"></span>Caldera Key</a>
  <nav class="main-nav">
    <a class="active" href="#">HOME</a><a href="#">ABOUT US</a><a href="#">TOUR PACKAGES</a><a href="#">BOOKING</a><a href="#">BLOG</a><a href="#">CONTACT</a>
  </nav>
</header>

<section class="hero" role="img" aria-label="Tropical beach with palm trees and turquoise sea">
  <div class="hero-slider" role="img" aria-label="City skyline across the harbour with a traditional boat on the water">
    <div class="hero-caption"><h2>CALDERA KEY</h2><p>THE ADVENTURE BEGINS</p></div>
    <div class="slider-arrows">
      <span><svg viewBox="0 0 10 10"><path d="M7 1 3 5l4 4"/></svg></span>
      <span><svg viewBox="0 0 10 10"><path d="M3 1l4 4-4 4"/></svg></span>
    </div>
  </div>
</section>

<section class="welcome">
  <h1>Welcome to <span>Caldera Key</span></h1>
  <p>Discover a small mountain town where cool breezes, coffee farms and rivers meet. Browse local businesses, read the latest town news and plan your stay with guided tours, trusted hotels and easy rentals. Our listings help visitors find what they need and help local owners reach new guests every single day of the year, from the highland trails down to the quiet valley markets and the friendly cafés around the plaza.</p>
</section>

<section class="features">
  <div class="feature">
    <div class="icon gold"><svg viewBox="0 0 24 24"><circle cx="12" cy="12" r="9"/><path d="M15 9l-2 5-4 1 2-5z"/></svg></div>
    <h3>SELLING GUIDED TOURS</h3>
    <p>Book trusted local guides for hikes, coffee farms and river trips, with clear prices and flexible dates.</p>
    <a class="more" href="#">Read More →</a>
  </div>
  <div class="feature">
    <div class="icon blue"><svg viewBox="0 0 24 24"><path d="M4 20V6h10v14M14 10h6v10M7 9h2M7 13h2M7 17h2M17 14h1"/></svg></div>
    <h3>HOTEL/HOSTELS</h3>
    <p>Compare cosy hostels, family rooms and boutique hotels close to the plaza and the mountain trails.</p>
    <a class="more" href="#">Read More →</a>
  </div>
  <div class="feature">
    <div class="icon green"><svg viewBox="0 0 24 24"><path d="M3 15l2-6h14l2 6v3H3z"/><circle cx="7" cy="18" r="1.5"/><circle cx="17" cy="18" r="1.5"/></svg></div>
    <h3>RENTAL VEHICLES</h3>
    <p>Reserve cars, scooters and bikes from local shops and explore the highlands at your own pace.</p>
    <a class="more" href="#">Read More →</a>
  </div>
</section>

<section class="hot">
  <div class="hot-list">
    <h2 class="section-title">Hot Destinations</h2>
    <article class="trip">
      <div class="trip-photo photo-a" role="img" aria-label="Hot air balloon over the valley at sunset"></div>
      <div class="trip-body">
        <h3>HOT BALOON SPECIAL JOURNEY</h3>
        <div class="trip-meta"><b>$124</b><span>★ 3 PEOPLE</span></div>
        <p>Float above coffee farms and cloud forest at sunrise, then enjoy a fresh breakfast with your crew on landing near the river.</p>
        <a class="btn-outline" href="#">VIEW DETAILS</a>
      </div>
    </article>
    <article class="trip">
      <div class="trip-photo photo-b" role="img" aria-label="Traveller resting on a hillside at golden hour"></div>
      <div class="trip-body">
        <h3>HOT BALOON SPECIAL JOURNEY</h3>
        <div class="trip-meta"><b>$124</b><span>★ 3 PEOPLE</span></div>
        <p>Float above coffee farms and cloud forest at sunrise, then enjoy a fresh breakfast with your crew on landing near the river.</p>
        <a class="btn-outline" href="#">VIEW DETAILS</a>
      </div>
    </article>
    <article class="trip">
      <div class="trip-photo photo-c" role="img" aria-label="Mountain peaks above a green lake"></div>
      <div class="trip-body">
        <h3>HOT BALOON SPECIAL JOURNEY</h3>
        <div class="trip-meta"><b>$124</b><span>★ 3 PEOPLE</span></div>
        <p>Float above coffee farms and cloud forest at sunrise, then enjoy a fresh breakfast with your crew on landing near the river.</p>
        <a class="btn-outline" href="#">VIEW DETAILS</a>
      </div>
    </article>
  </div>

  <aside class="sidebar">
    <div class="widget">
      <h4>TRAVEL WIDGET</h4>
      <p class="intro">Choose your dates and group size to see available trips and prices.</p>
      <div class="field">DESTINATION<span class="box"></span></div>
      <div class="field">ARRIVAL<span class="box"></span></div>
      <div class="field">DEPARTURE<span class="box"></span></div>
      <div class="field">ROOMS<span class="box"></span></div>
      <div class="field">PERSONS<span class="box"></span></div>
      <p class="note">Secure your spot with your advantage</p>
      <a class="btn-orange" href="#">SUBMIT NOW</a>
    </div>
    <div class="side-photo" role="img" aria-label="City tower at sunset"></div>
    <p class="side-text">Special weekend packages with guided walks, local dinners and a night in town.</p>
  </aside>
</section>

<section class="newsletter">
  <div><h4>JOIN OUR NEWSLETTER</h4><small>Get local news and deals every week</small></div>
  <div class="subscribe"><span>Enter your E-mail</span><b>SUBSCRIBE</b></div>
</section>

<footer class="site-footer">
  <div class="about">
    <h5>About Our Company</h5>
    <p>Caldera Key is the town guide for locals and visitors. We list businesses, share news and stories, and connect guests with tours, stays and rentals across the highlands. Listings are simple, affordable and easy to keep up to date.</p>
  </div>
  <div class="col">
    <h5>QUICK LINK</h5>
    <ul><li>Customer Feedback</li><li>Travel Policy</li><li>About Our Tours</li><li>Payment Guide</li><li>Best Hotel Offers</li></ul>
  </div>
  <div class="col">
    <h5>INFORMATION</h5>
    <ul><li>Getting Around</li><li>Accommodation</li><li>Travel and Health</li><li>Special Events</li><li>Refund and Privacy</li></ul>
  </div>
  <div class="col contact">
    <h5>CONTACT US</h5>
    <ul><li>Caldera Key PO Box 0417</li><li>Chiriqui Highlands</li><li>+507 555 0142</li><li>hello@calderakey.example</li></ul>
  </div>
</footer>

<div class="bottom-bar">
  <span>Copyright © 2015 Caldera Key. All Rights Reserved</span>
  <span>Terms &amp; Conditions &nbsp;|&nbsp; Privacy &amp; Disclaimer &nbsp;|&nbsp; Returns &amp; Refunds</span>
</div>

</body>
</html>
```